New manufacturing IT architecture concept powerpoint presentation

Create an appealing PowerPoint presentation, from handmade sketches, to illustrate a new approach to manufacturing IT architectures. We want to present the idea to augment the experience of people working in manufacturing plants using AI based on the data that our systems normally collect. We even want to present the power of having a tier 2 Manufacturing execution system that can coordinate and optimize production between multiple plants of the same corporate. The target audience is IT managers, Operations Managers, plant managers, engineering managers, and Continuous improvement managers.
Target Market(s)
Manufacturing companies mostly in Food & Bev and CPG. Mostly big multinational companies
Industry/Entity Type
Software manufacturing solutions (MES/MOM)
Font styles to use
Other font styles liked:
- Segoe
Look and feel

```html
<!DOCTYPE html>
<html lang="en">
<head>
<meta charset="utf-8">
<title>IOH APM – Presentation Slides</title>
<link href="https://fonts.googleapis.com/css2?family=Noto+Sans:wght@400;600;700;800&family=Roboto:wght@400;500;700&display=swap" rel="stylesheet">
<style>
  :root{
    --page:#dcdde0;
    --teal:#3aaeae;
    --white:#ffffff;
    --ink:#111111;
    --navy:#1b2a45;
    --green:#9ac33c;
    --magenta:#d6187a;
    --grid:#e2e4e6;
  }
  *{box-sizing:border-box;margin:0;padding:0}
  html,body{width:1200px;height:3824px;overflow:hidden;background:var(--page)}
  body{font-family:"Noto Sans",Verdana,sans-serif;position:relative}
  .slide{position:absolute;left:104px;width:1002px;height:563px;overflow:hidden;background:var(--white)}
  .s1{top:89px}.s2{top:697px}.s3{top:1304px}.s4{top:1911px}.s5{top:2517px}.s6{top:3124px}
  .brand{position:absolute;font-weight:800;font-size:27px;letter-spacing:1px;line-height:1}
  .brand.light{color:var(--white)}
  .brand.teal{color:var(--teal)}
  .photo{position:absolute}

  /* slide 1 */
  .s1 .photo{inset:0;background:linear-gradient(100deg,#1d2a38 0%,#2f4a5c 35%,#5d6a70 55%,#b5783a 75%,#2a3340 100%)}
  .s1 .title-box{position:absolute;left:616px;top:220px;width:386px;height:144px;background:rgba(20,22,26,.78);padding:20px 24px 20px 32px;color:var(--white);font-weight:800;font-size:24px;line-height:31px;letter-spacing:.8px}
  .s1 .brand{left:24px;top:518px}

  /* slide 2 */
  .s2 .panel{position:absolute;left:0;top:0;width:420px;height:563px;background:var(--teal)}
  .s2 .panel h2{position:absolute;left:69px;top:165px;width:300px;color:var(--white);font-weight:800;font-size:27px;line-height:31px;letter-spacing:.9px}
  .s2 .photo{left:420px;top:0;width:582px;height:563px;background:radial-gradient(circle at 60% 40%,#c49a6a 0%,#6b5036 45%,#2a2a2c 100%)}
  .s2 .brand{left:28px;top:515px}

  /* slide 3 */
  .s3 .chart-title{position:absolute;left:35px;top:27px;font-family:"Roboto",sans-serif;font-weight:700;font-size:16px;color:var(--ink)}
  .s3 .crumbs{position:absolute;right:32px;top:30px;font-family:"Roboto",sans-serif;font-weight:700;font-size:13px;color:var(--teal);letter-spacing:.3px}
  .s3 svg{position:absolute;left:0;top:0}
  .s3 .brand{left:34px;top:506px}

  /* slide 4 */
  .s4 .photo{inset:0;background:linear-gradient(90deg,#eef1f0 0%,#f6f8f8 50%,#eef1f0 100%)}
  .s4 svg{position:absolute;left:0;top:0}
  .s4 .brand{left:0;width:1002px;text-align:center;top:500px}
  .s4 .label{font-family:"Noto Sans",sans-serif;font-weight:700;font-size:15px;fill:var(--teal)}

  /* slide 5 */
  .s5 .photo{inset:0;background:linear-gradient(180deg,#ffffff 0%,#ffffff 25%,#c9ccd0 55%,#6e6a66 80%,#3a3a3e 100%)}
  .s5 .bubble{position:absolute;left:302px;top:-29px;width:400px;height:400px;border-radius:50%;background:linear-gradient(180deg,var(--teal) 0%,var(--teal) 55%,rgba(58,174,174,0) 88%)}
  .s5 h2{position:absolute;left:350px;top:38px;width:304px;text-align:center;color:var(--white);font-weight:800;font-size:27px;line-height:31px;letter-spacing:1.5px}
  .s5 p{position:absolute;left:377px;top:122px;width:250px;text-align:center;color:var(--white);font-size:15px;line-height:19px;letter-spacing:.3px}
  .s5 .brand{left:22px;top:22px}

  /* slide 6 */
  .s6 .photo{inset:0;background:linear-gradient(90deg,#f3f6f8 0%,#e6ecef 40%,#9aa7b8 65%,#2f3d5c 100%)}
  .s6 .thanks{position:absolute;left:105px;top:197px;width:281px;border-top:2px solid var(--navy);border-bottom:2px solid var(--navy);padding:6px 0 4px;font-weight:800;font-size:40px;line-height:48px;letter-spacing:1px;color:var(--navy);text-align:center;white-space:nowrap}
  .s6 .brand{left:33px;top:503px}
</style>
</head>
<body>

<section class="slide s1">
  <div class="photo" role="img" aria-label="Engineer in a hard hat operating a control panel with a tablet beside an industrial robot arm, overlaid with data graphics"></div>
  <div class="title-box">Integrated Operation Hub and Adaptive Production Management</div>
  <div class="brand light">IOH APM</div>
</section>

<section class="slide s2">
  <div class="panel"><h2>How digitalization evolved in last years from being technology focused to user and value focused</h2></div>
  <div class="photo" role="img" aria-label="Hands typing on a laptop at a wooden desk with glowing digital ring overlays"></div>
  <div class="brand light">IOH APM</div>
</section>

<section class="slide s3">
  <div class="chart-title">Competence</div>
  <div class="crumbs">WORKFORCE TURNOVER &#9656; MISSING EXPERIENCE</div>
  <svg width="1002" height="563" viewBox="0 0 1002 563" font-family="Roboto, sans-serif">
    <g stroke="var(--grid)" stroke-width="1">
      <line x1="55" y1="126" x2="965" y2="126"/><line x1="55" y1="157" x2="965" y2="157"/>
      <line x1="55" y1="188" x2="965" y2="188"/><line x1="55" y1="219" x2="965" y2="219"/>
      <line x1="55" y1="250" x2="965" y2="250"/><line x1="55" y1="281" x2="965" y2="281"/>
      <line x1="55" y1="313" x2="965" y2="313"/><line x1="55" y1="344" x2="965" y2="344"/>
      <line x1="55" y1="375" x2="965" y2="375"/><line x1="55" y1="406" x2="965" y2="406"/>
      <line x1="55" y1="437" x2="965" y2="437"/>
      <line x1="55" y1="126" x2="55" y2="437"/><line x1="131" y1="126" x2="131" y2="437"/>
      <line x1="207" y1="126" x2="207" y2="437"/><line x1="283" y1="126" x2="283" y2="437"/>
      <line x1="359" y1="126" x2="359" y2="437"/><line x1="434" y1="126" x2="434" y2="437"/>
      <line x1="510" y1="126" x2="510" y2="437"/><line x1="586" y1="126" x2="586" y2="437"/>
      <line x1="662" y1="126" x2="662" y2="437"/><line x1="738" y1="126" x2="738" y2="437"/>
      <line x1="814" y1="126" x2="814" y2="437"/><line x1="889" y1="126" x2="889" y2="437"/>
      <line x1="965" y1="126" x2="965" y2="437"/>
    </g>
    <g font-size="8" fill="#333" text-anchor="end">
      <text x="47" y="129">100</text><text x="47" y="160">90</text><text x="47" y="191">80</text>
      <text x="47" y="222">70</text><text x="47" y="253">60</text><text x="47" y="284">50</text>
      <text x="47" y="316">40</text><text x="47" y="347">30</text><text x="47" y="378">20</text>
      <text x="47" y="409">10</text><text x="47" y="440">0</text>
    </g>
    <g font-size="8" fill="#333" text-anchor="middle">
      <text x="93" y="460">JAN</text><text x="169" y="460">FEB</text><text x="245" y="460">MAR</text>
      <text x="321" y="460">APR</text><text x="397" y="460">MAY</text><text x="472" y="460">JUN</text>
      <text x="548" y="460">JUL</text><text x="624" y="460">AUG</text><text x="700" y="460">SEP</text>
      <text x="776" y="460">OCT</text><text x="852" y="460">NOV</text><text x="927" y="460">DEC</text>
    </g>
    <polyline fill="none" stroke="var(--green)" stroke-width="2"
      points="55,313 131,281 207,313 283,219 359,219 434,250 510,219 586,219 662,170 738,157 814,157 889,170 965,157"/>
    <g fill="var(--green)">
      <circle cx="55" cy="313" r="3.5"/><circle cx="131" cy="281" r="3.5"/><circle cx="207" cy="313" r="3.5"/>
      <circle cx="283" cy="219" r="3.5"/><circle cx="359" cy="219" r="3.5"/><circle cx="434" cy="250" r="3.5"/>
      <circle cx="510" cy="219" r="3.5"/><circle cx="586" cy="219" r="3.5"/><circle cx="662" cy="170" r="3.5"/>
      <circle cx="738" cy="157" r="3.5"/><circle cx="814" cy="157" r="3.5"/><circle cx="889" cy="170" r="3.5"/>
      <circle cx="965" cy="157" r="3.5"/>
    </g>
    <polyline fill="none" stroke="var(--magenta)" stroke-width="2"
      points="55,406 131,344 207,375 283,281 359,250 434,313 510,281 586,313 738,188 889,250 965,188"/>
    <g fill="var(--magenta)">
      <circle cx="55" cy="406" r="3.5"/><circle cx="131" cy="344" r="3.5"/><circle cx="207" cy="375" r="3.5"/>
      <circle cx="283" cy="281" r="3.5"/><circle cx="359" cy="250" r="3.5"/><circle cx="434" cy="313" r="3.5"/>
      <circle cx="510" cy="281" r="3.5"/><circle cx="586" cy="313" r="3.5"/><circle cx="738" cy="188" r="3.5"/>
      <circle cx="889" cy="250" r="3.5"/><circle cx="965" cy="188" r="3.5"/>
    </g>
    <text x="434" y="224" font-size="11" fill="#111" text-anchor="middle">Knowledge</text>
    <text x="0" y="0" font-size="11" fill="#111" transform="translate(690,250) rotate(-42)">Experience</text>
  </svg>
  <div class="brand teal">IOH APM</div>
</section>

<section class="slide s4">
  <div class="photo" role="img" aria-label="Faded office background with a team of colleagues"></div>
  <svg width="1002" height="563" viewBox="0 0 1002 563">
    <defs>
      <radialGradient id="teamFill" cx="50%" cy="55%" r="60%">
        <stop offset="0%" stop-color="#b89a7e"/><stop offset="60%" stop-color="#8f8a86"/><stop offset="100%" stop-color="#c8ccce"/>
      </radialGradient>
    </defs>
    <circle cx="496" cy="279" r="163" fill="url(#teamFill)" stroke="var(--teal)" stroke-width="8" role="img" aria-label="Team of smiling colleagues gathered around laptops in a bright office"/>
    <g fill="var(--teal)" stroke="var(--white)" stroke-width="3">
      <circle cx="496" cy="120" r="38"/><circle cx="356" cy="187" r="38"/><circle cx="316" cy="279" r="38"/>
      <circle cx="347" cy="384" r="38"/><circle cx="652" cy="187" r="38"/><circle cx="690" cy="279" r="38"/>
      <circle cx="661" cy="384" r="38"/>
    </g>
    <g fill="none" stroke="var(--white)" stroke-width="2.5" stroke-linecap="round" stroke-linejoin="round">
      <circle cx="484" cy="108" r="4"/><path d="M484 114v14M478 120h12M480 136l4-8 4 8"/><rect x="492" y="104" width="18" height="14"/><path d="M494 132l6-14 6 14"/>
      <circle cx="356" cy="183" r="9"/><path d="M352 195h8M353 200h6M356 166v-5M340 183h-5M372 183h5M344 171l-4-4M368 171l4-4"/>
      <rect x="302" y="272" width="18" height="10" rx="5" transform="rotate(-45 311 277)"/><rect x="312" y="276" width="18" height="10" rx="5" transform="rotate(-45 321 281)"/>
      <path d="M331 386h32M335 386v10M359 386v10"/><circle cx="347" cy="372" r="4"/><circle cx="334" cy="376" r="3"/><circle cx="360" cy="376" r="3"/><path d="M347 378v8"/>
      <rect x="638" y="175" width="28" height="19" rx="2"/><path d="M632 199h40"/><path d="M652 181v1M652 185v5"/>
      <circle cx="690" cy="279" r="6"/><circle cx="690" cy="279" r="13" stroke-dasharray="5 3"/>
      <path d="M661 372l-8 10M661 372l8 10M661 372v12M661 384l-9 13M661 384l9 13"/>
    </g>
    <text class="label" x="496" y="72" text-anchor="middle">Train</text>
    <text class="label" x="310" y="189" text-anchor="end">Skill</text>
    <text class="label" x="698" y="193">Inform</text>
    <text class="label" x="275" y="284" text-anchor="end">Connect</text>
    <text class="label" x="737" y="285">Augment</text>
    <text class="label" x="304" y="393" text-anchor="end">Coordinate</text>
    <text class="label" x="704" y="399">Unify</text>
  </svg>
  <div class="brand teal">IOH APM</div>
</section>

<section class="slide s5">
  <div class="photo" role="img" aria-label="Business team laughing around a meeting table with laptops and water bottles"></div>
  <div class="bubble"></div>
  <h2>PRODUCTION FORECAST</h2>
  <p>Analysis of production, line and environment status to forecast production volumes or completion</p>
  <div class="brand teal">IOH APM</div>
</section>

<section class="slide s6">
  <div class="photo" role="img" aria-label="Three smiling colleagues in suits looking at a laptop by a bright window"></div>
  <div class="thanks">THANK YOU</div>
  <div class="brand teal">IOH APM</div>
</section>

</body>
</html>
```